Popcorn, ice cream, alcohol infused shakes shop

Create a clean simple website with pictures and bold type for a popcorn, ice cream and boozy shake shop. The site should have:
- Unique and Large Typography
- Large & Responsive Hero (stunning, elicits a response) Images.No concern with above or below the fold. Create a strong visual experience that encourages visitors to scroll down to read more. Use large images to visually tell a story without having to rely on just text.
- Flat image designs
- Place for me to upload an ad type video
- Hidden type menu (three line menu)
- A few small card like images (food, gift bags, tins, etc.) menu items with a brief description.

Target Market(s)

21-49 years of age for the boozy shakes. Soccer moms for sports teams & sleepovers, professionals (teachers, realtors, pharm sales), gifts for family and friends. Also some kids

Coding

Coded - Design and coding required

Number of Pages Required

5+ page

Font styles to use
Sans Serif

Colors

Designer to choose colors to be used in the design.

Requirements
Must have
• Images of gourmet popcorn, fancy shakes, ice cream, gift bags and popcorn tins. Holiday popcorn tins and gift bags along with grift certificates. Ability for visitors to send a contact form to kt@treatloft.example
• Five pages - Home Page, AboutUs, Menu, Gift/Promotion, Contact Us
Nice to have
• Smooth flow on the home page. Mostly images and bold text.
Should not have
• Too many words. Boring text fonts

```html
<!DOCTYPE html>
<html lang="en">
<head>
<meta charset="utf-8">
<title>Treat Loft — Ice Cream, Popcorn &amp; Boozy Shakes</title>
<link rel="stylesheet" href="https://fonts.googleapis.com/css2?family=Archivo+Black&family=Arimo:ital,wght@0,400;0,700;1,400;1,700&display=swap">
<style>
  :root {
    --hero-top: #e75c88;
    --hero-bottom: #df2f3b;
    --menu-red: #e5262d;
    --green: #8cc43f;
    --white: #ffffff;
    --ink: #222222;
    --body-grey: #555555;
    --card-line: #bdbdbd;
    --events-yellow: #e4dc3a;
    --cyan: #03bdd3;
    --button-cyan: #13b7d3;
    --sun-yellow: #f4ec33;
    --footer-text: #333333;
    --head-font: "Archivo Black", "Arial Black", sans-serif;
    --body-font: "Arimo", Arial, sans-serif;
  }
  * { box-sizing: border-box; margin: 0; padding: 0; }
  html, body { width: 1200px; height: 3990px; overflow: hidden; }
  body { position: relative; background: var(--white); font-family: var(--body-font); }
  .abs { position: absolute; }

  /* Hero */
  .hero { left: 0; top: 0; width: 1200px; height: 755px;
    background: linear-gradient(180deg, var(--hero-top) 0%, var(--hero-bottom) 100%); }
  .brand { left: 100px; top: 62px; display: flex; align-items: center; gap: 12px;
    font-family: var(--head-font); font-size: 34px; color: var(--white); letter-spacing: 0.5px; }
  .brand-dot { width: 22px; height: 22px; background: var(--green); border-radius: 50%; }
  .menu-toggle { left: 1030px; top: 37px; width: 66px; height: 67px; background: var(--menu-red);
    display: flex; flex-direction: column; justify-content: center; align-items: center; gap: 6px; }
  .menu-toggle span { display: block; width: 34px; height: 5px; background: var(--white); border-radius: 2px; }
  .hero-title { left: 30px; top: 312px; width: 700px; text-align: center; color: var(--white);
    font-family: var(--head-font); font-size: 70px; line-height: 64px; letter-spacing: -1.5px; }
  .hero-sub { left: 20px; top: 464px; width: 720px; text-align: center; color: var(--white);
    font-family: var(--head-font); font-size: 58px; line-height: 54px; letter-spacing: -1.5px; }
  .hero-photo { left: 813px; top: 217px; width: 387px; height: 538px;
    background: linear-gradient(180deg, rgba(240,197,181,0.55) 0%, rgba(198,74,79,0.55) 100%); }

  /* Features */
  .features { left: 0; top: 755px; width: 1200px; height: 675px; }
  .features svg { position: absolute; left: 0; top: 0; }
  .cone-photo { left: 116px; top: 813px; width: 271px; height: 580px;
    background: linear-gradient(180deg, #d9465f 0%, #a9455a 45%, #5a4543 100%); opacity: 0.85; }
  .feature-card { width: 319px; border: 2px solid rgba(255,255,255,0.85); border-radius: 7px;
    color: var(--white); text-align: center; font-weight: 700; font-size: 15.5px; line-height: 23px;
    display: flex; flex-direction: column; align-items: center; justify-content: center; padding: 6px 6px 12px; }
  .feature-card svg { width: 50px; height: 48px; margin-bottom: 12px; flex-shrink: 0; }

  /* Gallery */
  .gallery { left: 0; top: 1430px; width: 1200px; height: 533px; display: grid;
    grid-template-columns: 400px 400px 400px; grid-template-rows: 266px 267px; }
  .tile-sundae { background: linear-gradient(160deg, #5a2a1c, #2a120b 60%, #7a4a2a); }
  .tile-shake { background: linear-gradient(160deg, #a5877a, #7f5f55 50%, #c9b2a0); }
  .tile-popcorn-bowl { background: linear-gradient(180deg, #e9e6ee 0%, #c6d7a0 55%, #e4b34c 100%); }
  .tile-scoop { background: linear-gradient(160deg, #9aa4b6, #e7d9b8 50%, #c89b4e); }
  .tile-popcorn-mix { background: linear-gradient(135deg, #c83c2a, #6e9a2a 35%, #d8c02a 65%, #b22a25); }
  .tile-iced-drink { background: linear-gradient(150deg, #3a2612, #8a6036 50%, #d2b28a); }

  /* Shop cards */
  .shop-heading { left: 0; top: 2004px; width: 1200px; text-align: center; color: var(--green);
    font-family: var(--head-font); font-size: 64px; letter-spacing: -1.5px; }
  .shop-card { width: 338px; border: 1.5px solid var(--card-line); background: var(--white); text-align: center; }
  .shop-card .shot { width: 100%; height: 238px; }
  .shop-card h3 { font-family: var(--head-font); font-size: 20px; color: var(--ink); margin: 28px 0 20px; font-weight: 400; }
  .shop-card p { font-size: 16.5px; line-height: 30px; color: var(--body-grey); padding: 0 14px 10px; }
  .shot-giftbags { background: linear-gradient(160deg, #f2efe9, #c83a34 45%, #3f8a4a 70%, #efe7d8); }
  .shot-tins { background: linear-gradient(160deg, #c9182b, #f0c43a 35%, #d62a34 65%, #e9e9ee); }
  .shot-food { background: linear-gradient(160deg, #6a3a22, #ecdcd0 55%, #f3f3f3); }

  /* Events */
  .events { left: 0; top: 2644px; width: 1200px; height: 506px;
    background: radial-gradient(ellipse at 30% 30%, #efe56a 0%, var(--events-yellow) 45%, #d6cd33 100%); }
  .events-title { left: 65px; top: 2770px; color: var(--white); font-family: var(--head-font);
    font-size: 62px; line-height: 64px; letter-spacing: -1.5px; }
  .events-text { left: 65px; top: 2928px; width: 480px; color: var(--white); font-size: 15.5px;
    font-weight: 400; line-height: 30px; }
  .events-button { left: 133px; top: 3000px; width: 334px; height: 45px; background: var(--button-cyan);
    color: var(--white); font-size: 25px; display: flex; align-items: center; justify-content: center; }
  .video { left: 600px; top: 2749px; width: 533px; height: 296px;
    background: linear-gradient(135deg, #5a5a5a, #1c1c1c 45%, #8a8a8a 80%, #bdbdbd); }
  .video svg { position: absolute; left: 0; top: 0; }

  /* Contact */
  .contact { left: 0; top: 3150px; width: 1200px; height: 580px; background: var(--cyan); }
  .shake-photo { left: 73px; top: 3176px; width: 388px; height: 513px;
    background: linear-gradient(180deg, #ffffff 0%, #f2d2cd 50%, #ffffff 100%); }
  .contact-kicker { left: 600px; top: 3290px; color: var(--sun-yellow); font-size: 19px; font-style: italic; }
  .contact-title { left: 600px; top: 3314px; color: var(--white); font-family: var(--head-font);
    font-size: 70px; line-height: 59px; letter-spacing: -1.5px; }
  .contact-button { left: 600px; top: 3561px; width: 196px; height: 40px; background: var(--sun-yellow);
    color: var(--button-cyan); font-size: 14px; font-weight: 700; font-style: italic;
    display: flex; align-items: center; justify-content: center; }

  /* Footer */
  .footer-band { left: 0; top: 3690px; width: 1200px; height: 300px; }
  .social { top: 3790px; width: 20px; height: 20px; border-radius: 50%; background: #9a9a9a; }
  .address { left: 700px; top: 3832px; width: 424px; text-align: right; color: var(--footer-text);
    font-size: 16.5px; line-height: 30px; font-style: normal; }
</style>
</head>
<body>

  <header class="abs hero"></header>
  <div class="abs brand"><span class="brand-dot"></span>Treat Loft</div>
  <nav class="abs menu-toggle" aria-label="Menu"><span></span><span></span><span></span></nav>
  <h1 class="abs hero-title">GET YOUR SNACK ON!</h1>
  <p class="abs hero-sub">Ice cream, popcorn, shakes and boozy shakes.</p>
  <div class="abs hero-photo" role="img" aria-label="Young woman in a red plaid shirt sipping a pink milkshake"></div>

  <section class="abs features">
    <svg width="1200" height="675" viewBox="0 0 1200 675">
      <polygon points="0,282 1200,64 1200,675 0,675" fill="#8cc43f"/>
    </svg>
  </section>
  <div class="abs cone-photo" role="img" aria-label="Scoop of red sorbet in a dark waffle cone"></div>

  <div class="abs feature-card" style="left:526px; top:926px; height:168px;">
    <svg viewBox="0 0 24 24"><path fill="#fff" d="M12 1.8l3.1 6.6 7.2.8-5.4 4.9 1.5 7.1L12 17.6l-6.4 3.6 1.5-7.1-5.4-4.9 7.2-.8z"/></svg>
    Delicious shakes and boozy shakes. Ask our employees and have your order packed up to take home
  </div>
  <div class="abs feature-card" style="left:526px; top:1115px; height:143px;">
    <svg viewBox="0 0 24 24"><path fill="#fff" d="M12 1.8l3.1 6.6 7.2.8-5.4 4.9 1.5 7.1L12 17.6l-6.4 3.6 1.5-7.1-5.4-4.9 7.2-.8z"/></svg>
    Made fresh daily. We make our popcorn fresh.
  </div>
  <div class="abs feature-card" style="left:862px; top:882px; height:145px;">
    <svg viewBox="0 0 24 24"><path fill="#fff" d="M12 1.8l3.1 6.6 7.2.8-5.4 4.9 1.5 7.1L12 17.6l-6.4 3.6 1.5-7.1-5.4-4.9 7.2-.8z"/></svg>
    For early birds and night owls. We are open from 10:30 am to late evening.
  </div>
  <div class="abs feature-card" style="left:862px; top:1046px; height:146px;">
    <svg viewBox="0 0 24 24"><path fill="#fff" d="M12 1.8l3.1 6.6 7.2.8-5.4 4.9 1.5 7.1L12 17.6l-6.4 3.6 1.5-7.1-5.4-4.9 7.2-.8z"/></svg>
    Also for vegans. We also offer non-dairy shakes for our vegen guests.
  </div>

  <section class="abs gallery">
    <div class="tile-sundae" role="img" aria-label="Chocolate sundae in a cone topped with a cherry"></div>
    <div class="tile-shake" role="img" aria-label="Chocolate freakshake with cake against a brick wall"></div>
    <div class="tile-popcorn-bowl" role="img" aria-label="Green cup overflowing with colourful popcorn"></div>
    <div class="tile-scoop" role="img" aria-label="Vanilla ice cream with caramel and caramel popcorn"></div>
    <div class="tile-popcorn-mix" role="img" aria-label="Close view of red, green and yellow popcorn"></div>
    <div class="tile-iced-drink" role="img" aria-label="Iced coffee shake with a straw on a wooden table"></div>
  </section>

  <h2 class="abs shop-heading">Take it home or order online</h2>

  <article class="abs shop-card" style="left:74px; top:2170px;">
    <div class="shot shot-giftbags" role="img" aria-label="Holiday popcorn gift bags tied with red ribbon"></div>
    <h3>Giftbags</h3>
    <p>Lorem ipsum dolor sit amet, consectetur adipiscing elit. Ut elit tellus, luctus nec ullamcorper mattis, pulvinar dapibus leo.</p>
  </article>
  <article class="abs shop-card" style="left:430px; top:2170px;">
    <div class="shot shot-tins" role="img" aria-label="Red heart-shaped tin filled with jelly beans"></div>
    <h3>Tins</h3>
    <p>Lorem ipsum dolor sit amet, consectetur adipiscing elit. Ut elit tellus, luctus nec ullamcorper mattis, pulvinar dapibus leo.</p>
  </article>
  <article class="abs shop-card" style="left:786px; top:2170px;">
    <div class="shot shot-food" role="img" aria-label="Brownies with a scoop of ice cream on a plate"></div>
    <h3>Food</h3>
    <p>Lorem ipsum dolor sit amet, consectetur adipiscing elit. Ut elit tellus, luctus nec ullamcorper mattis, pulvinar dapibus leo.</p>
  </article>

  <section class="abs events" role="img" aria-label="Friends laughing and sharing shakes, tinted yellow"></section>
  <h2 class="abs events-title">We organize<br>events</h2>
  <p class="abs events-text">Lorem ipsum dolor sit amet, consectetur adipiscing elit. Ut elit tellus, luctus nec ullamcorper mattis, pulvinar dapibus leo.</p>
  <a class="abs events-button">Have a look at our menu</a>
  <div class="abs video" role="img" aria-label="Promotional video still: astronaut beside a flag on the moon">
    <svg width="533" height="296" viewBox="0 0 533 296">
      <circle cx="267" cy="146" r="42" fill="rgba(0,0,0,0.25)" stroke="rgba(255,255,255,0.6)" stroke-width="4"/>
      <polygon points="255,126 255,166 288,146" fill="rgba(255,255,255,0.6)"/>
    </svg>
  </div>

  <section class="abs contact"></section>
  <div class="abs shake-photo" role="img" aria-label="Strawberry milkshake in a tall glass topped with a cherry and mint"></div>
  <p class="abs contact-kicker">Only The Best For You</p>
  <h2 class="abs contact-title">Visit us or<br>send us a<br>message</h2>
  <a class="abs contact-button">Contact Us Today &raquo;</a>

  <footer class="abs footer-band">
    <svg width="1200" height="300" viewBox="0 0 1200 300">
      <polygon points="0,30 1200,0 1200,300 0,300" fill="#f4ec33"/>
    </svg>
  </footer>
  <span class="abs social" style="left:1058px;" aria-label="Social link"></span>
  <span class="abs social" style="left:1101px;" aria-label="Social link"></span>
  <address class="abs address">820 Maple Grove Ave #14,<br>Cedar Hollow TX 70000<br>(555) 013-4470</address>

</body>
</html>
```